Shop Front Design

We are Corwick Fusion Stores, a welding products suppliers just north of London.
We would like a banner 4.0m x 1.5m that will be placed above our building entrance to introduce our business to regular and new customers. Info we would like lister:
-Our Logo (CFS logo1)
-Core info: email address, phone number, opening hours
cfsarc@mailvane.net
07412 580 317
Monday to Friday 12:00 - 18:00
Saturday 09:00 - 12:00
-Our core services:
Welders & Consumables
Hire
Industrial Gases
Training Courses
-Our core suppliers logos. I would like to see what impact they would have on the banner
Preferred colour theme orange and grey.

```html
<!DOCTYPE html>
<html lang="en">
<head>
<meta charset="utf-8">
<title>Corwick Fusion Stores – Shop Front Banner</title>
<link rel="stylesheet" href="https://fonts.googleapis.com/css2?family=Montserrat:wght@400;500;600;700;800&display=swap">
<style>
  :root {
    --page: #ffffff;
    --banner: #2c3235;
    --brand-orange: #e8922a;
    --service-red: #e34a24;
    --divider: #e5534b;
    --contact: #d2703a;
    --shadow: #e3e3e3;
  }
  * { margin: 0; padding: 0; box-sizing: border-box; }
  html, body {
    width: 1200px; height: 1200px; overflow: hidden;
    background: var(--page);
    font-family: "Montserrat", sans-serif;
  }
  .banner {
    position: absolute; left: 182px; top: 106px;
    width: 848px; height: 325px;
    background: var(--banner);
    box-shadow: 5px 7px 0 var(--shadow);
  }
  .brand {
    position: absolute; left: 42px; top: 70px; width: 350px;
    display: flex; align-items: center; gap: 12px;
  }
  .brand-dot {
    flex: none; width: 18px; height: 18px; border-radius: 50%;
    background: var(--brand-orange);
  }
  .brand-name {
    color: var(--brand-orange);
    font-weight: 800; font-size: 31px; line-height: 1.05;
    letter-spacing: 0.5px; text-transform: uppercase;
  }
  .contact { position: absolute; left: 33px; top: 212px; color: var(--contact); }
  .contact-row { display: flex; align-items: center; gap: 6px; margin-bottom: 5px; }
  .contact-row svg { flex: none; width: 22px; height: 22px; }
  .contact-hours { font-size: 10.5px; line-height: 1.2; letter-spacing: 0.4px; }
  .contact-text { font-size: 14px; letter-spacing: 0.6px; }
  .divider {
    position: absolute; left: 418px; top: 62px;
    width: 7px; height: 180px; background: var(--divider);
  }
  .services { position: absolute; left: 458px; top: 88px; color: var(--service-red); }
  .services-head { display: flex; align-items: flex-end; gap: 4px; }
  .services-icon { width: 54px; height: 38px; background: var(--service-red); border-radius: 4px; opacity: 0.9; }
  .services-title { font-weight: 700; font-size: 24.5px; letter-spacing: 0.2px; line-height: 1; }
  .service-list { list-style: none; margin: 10px 0 0 57px; }
  .service-list li { font-size: 19.5px; line-height: 22px; font-weight: 500; }
  .service-list li::before { content: "•"; margin-right: 7px; font-size: 16px; }
  .service-list li:last-child { margin-top: 3px; }
</style>
</head>
<body>
  <section class="banner">
    <div class="brand">
      <span class="brand-dot"></span>
      <span class="brand-name">Corwick Fusion Stores</span>
    </div>

    <div class="contact">
      <div class="contact-row">
        <svg viewBox="0 0 24 24" fill="none" stroke="currentColor" stroke-width="1.6"><circle cx="12" cy="12" r="10"/><path d="M11 6v6.5l3.5 2.5"/></svg>
        <p class="contact-hours">Monday to Friday 12:00<br>18:00 Saturday 09:00 - 12:00</p>
      </div>
      <div class="contact-row">
        <svg viewBox="0 0 24 24" fill="none" stroke="currentColor" stroke-width="1.6"><rect x="2.5" y="5" width="19" height="14"/><path d="M2.5 5l9.5 8 9.5-8"/></svg>
        <p class="contact-text">cfsarc@mailvane.net</p>
      </div>
      <div class="contact-row">
        <svg viewBox="0 0 24 24" fill="none" stroke="currentColor" stroke-width="1.6"><circle cx="12" cy="12" r="10"/><path d="M8 6.5l2 2.5-1 1.5c.8 1.8 2 3 3.8 3.8l1.5-1 2.5 2-1 1.7c-4.5-.3-8.3-4-8.7-8.7z" fill="currentColor"/></svg>
        <p class="contact-text">07412 580 317</p>
      </div>
    </div>

    <div class="divider"></div>

    <div class="services">
      <div class="services-head">
        <div class="services-icon" role="img" aria-label="Welding glove and wrench icon"></div>
        <h2 class="services-title">OUR CORE SERVICES</h2>
      </div>
      <ul class="service-list">
        <li>Welders &amp; Consumables</li>
        <li>Training Courses</li>
        <li>Industrial Gases</li>
        <li>Hire</li>
      </ul>
    </div>
  </section>
</body>
</html>
```